Simple and clean

We need a business card design for a new company called Dwelling Hawk. It is a search engine to find current properties for sale or rent in New Zealand market.
We have already a colour scheme that we would like people to use.
Light brown: #D4CCB0
Light green: #D6E4D4
Green: #669966
Black/White
It is OK to divert from this colour scheme slightly as long as there is a green component to the business card.
Final design should be clean, simple and should communicate the nature of the business.
Target Market(s)
- First home buyers
- Real estate agents
- People seeking rentals
Industry/Entity Type
Business
Requirements
Must have
- Use those or similar colours.
Light brown: #D4CCB0
Light green: #D6E4D4
Green: #669966
Black/White

```html
<!DOCTYPE html>
<html lang="en">
<head>
<meta charset="utf-8">
<title>Dwelling Hawk – Business Card</title>
<link rel="stylesheet" href="https://fonts.googleapis.com/css2?family=Arimo:wght@400;700&display=swap">
<style>
  :root {
    --light-brown: #D4CCB0;
    --light-green: #D6E4D4;
    --green: #669966;
    --ink: #111111;
    --black: #000000;
    --white: #ffffff;
  }
  html, body {
    margin: 0;
    padding: 0;
    overflow: hidden;
    background: var(--white);
  }
  .card {
    position: relative;
    width: 1200px;
    height: 694px;
    overflow: hidden;
    background: var(--white);
    font-family: "Arimo", Arial, sans-serif;
    color: var(--ink);
  }
  .header-band {
    position: absolute;
    left: 0; top: 143px;
    width: 1200px; height: 91px;
    background: var(--light-green);
  }
  .brand-disc {
    position: absolute;
    left: 29px; top: 47px;
    width: 164px; height: 164px;
    border-radius: 50%;
    background: var(--white);
  }
  .brand {
    position: absolute;
    left: 86px; top: 72px;
    display: flex;
    align-items: center;
    gap: 22px;
  }
  .brand-mark {
    width: 92px; height: 92px;
    border-radius: 50%;
    background: var(--green);
  }
  .brand-name {
    font-size: 54px;
    font-weight: 700;
    letter-spacing: -0.5px;
    color: var(--ink);
    line-height: 1;
  }
  .motto-panel {
    position: absolute;
    left: 0; top: 234px;
    width: 582px; height: 342px;
    background: var(--light-brown);
  }
  .motto {
    position: absolute;
    left: 66px; top: 280px;
    margin: 0; padding: 0;
    list-style: none;
  }
  .motto-item {
    display: flex;
    align-items: center;
    height: 50px;
    margin-bottom: 51px;
    font-size: 40px;
    font-weight: 700;
    letter-spacing: 0.5px;
  }
  .initial {
    position: relative;
    display: inline-flex;
    align-items: center;
    justify-content: center;
    width: 46px; height: 50px;
    margin-right: 6px;
  }
  .initial svg {
    position: absolute;
    inset: 0;
  }
  .contact {
    position: absolute;
    left: 582px; top: 234px;
    width: 618px; height: 342px;
    text-align: center;
    font-weight: 700;
  }
  .person-name {
    position: absolute;
    left: 0; right: 0; top: 96px;
    margin: 0;
    font-size: 28px;
    letter-spacing: 0.3px;
  }
  .person-role {
    position: absolute;
    left: 0; right: 0; top: 133px;
    margin: 0;
    font-size: 20px;
  }
  .contact-line {
    position: absolute;
    left: 0; right: 0;
    margin: 0;
    font-size: 22px;
  }
  .contact-mobile { top: 267px; }
  .contact-email  { top: 303px; font-size: 21px; }
  .web-band {
    position: absolute;
    left: 0; top: 576px;
    width: 1200px; height: 118px;
    background: var(--black);
  }
  .web-address {
    position: absolute;
    left: 0; top: 0;
  }
  .web-address text {
    font-family: "Arimo", Arial, sans-serif;
    font-weight: 700;
    font-size: 54px;
    fill: var(--green);
  }
</style>
</head>
<body>
<div class="card">
  <div class="header-band"></div>
  <div class="brand-disc"></div>
  <div class="brand">
    <span class="brand-mark"></span>
    <span class="brand-name">Dwelling Hawk</span>
  </div>

  <div class="motto-panel"></div>
  <ul class="motto">
    <li class="motto-item">
      <span class="initial">
        <svg width="46" height="50" viewBox="0 0 46 50" fill="none" stroke="#669966" stroke-width="2.5">
          <path d="M1 12V1H12M34 1H45V12M45 38V49H34M12 49H1V38"/>
        </svg>L</span>ocate
    </li>
    <li class="motto-item">
      <span class="initial">
        <svg width="46" height="50" viewBox="0 0 46 50" fill="none" stroke="#669966" stroke-width="2.5">
          <path d="M1 12V1H12M34 1H45V12M45 38V49H34M12 49H1V38"/>
        </svg>E</span>valuate
    </li>
    <li class="motto-item">
      <span class="initial">
        <svg width="46" height="50" viewBox="0 0 46 50" fill="none" stroke="#669966" stroke-width="2.5">
          <path d="M1 12V1H12M34 1H45V12M45 38V49H34M12 49H1V38"/>
        </svg>A</span>ccommodate
    </li>
  </ul>

  <div class="contact">
    <p class="person-name">Marcel Dubois</p>
    <p class="person-role">Director</p>
    <p class="contact-line contact-mobile">Mobile: 0432 555 010</p>
    <p class="contact-line contact-email">Email: marceldubois@dwellinghawk.co.nz</p>
  </div>

  <div class="web-band">
    <svg class="web-address" width="1200" height="118" viewBox="0 0 1200 118">
      <text x="44" y="76" textLength="1100" lengthAdjust="spacing">www.dwellinghawk.co.nz</text>
    </svg>
  </div>
</div>
</body>
</html>
```